Shopify Web-Page "Tiny-ThreadDays

We are building a new business in Switzerland offering premium sewing holiday camps for kids aged 9–14. In enclosed brief outlines our requirements for a complete Shopify homepage design and a multilingual logo creation.
Domains: tiny-threaddays.ch ; tiny-giornifilo.ch ; tiny-fadentage.ch

Project Overview
We are looking for:
1. A modern, fully designed Shopify homepage in English using standard Shopify content blocks (no custom coding), which we can later update ourselves. Supporting Multilanguage (EN, German, Italian).

2. A logo design that includes the brand identity and communicates our multilingual, creative, and child-focused positioning.

All details in enclosed

```html
<!DOCTYPE html>
<html lang="en">
<head>
<meta charset="utf-8">
<title>Tiny-ThreadDays – Sewing Holiday Camps</title>
<link href="https://fonts.googleapis.com/css2?family=Nunito+Sans:wght@400;600;700;800&family=Oswald:wght@700&display=swap" rel="stylesheet">
<style>
:root{
  --teal:#6fb0a6;
  --salmon:#f2a894;
  --ink:#1d1d1d;
  --text:#555;
  --band:#0e0e0e;
  --footer:#1b1b1b;
  --line:#d6d6d6;
  --white:#fff;
}
*{box-sizing:border-box;margin:0;padding:0}
html,body{width:1200px;height:4898px;overflow:hidden}
body{font-family:"Nunito Sans",Arial,sans-serif;color:var(--ink);background:var(--white);position:relative}
.abs{position:absolute}
.btn{display:inline-block;background:var(--salmon);color:var(--ink);font-weight:700;font-size:14px;border-radius:22px;padding:10px 30px;text-decoration:none}

.promo{left:0;top:0;width:1200px;height:30px;background:var(--teal);color:#fff;font-size:13px;text-align:center;line-height:30px;z-index:3}
.hero{left:0;top:30px;width:1200px;height:607px;
  background:
    radial-gradient(ellipse 260px 300px at 470px 330px,rgba(150,110,85,.55),transparent 70%),
    radial-gradient(ellipse 260px 320px at 820px 300px,rgba(140,120,110,.5),transparent 70%),
    linear-gradient(90deg,#2e3230 0%,#4a4540 35%,#5b534b 60%,#3a3733 100%)}
.hero::after{content:"";position:absolute;inset:0;background:rgba(0,0,0,.3)}
.header{left:0;top:30px;width:1200px;height:110px;z-index:2;color:#fff}
.header .tools{left:140px;top:30px;display:flex;gap:34px;align-items:center;font-size:12px}
.flag{width:26px;height:26px;border-radius:50%;background:#fff;display:inline-block;vertical-align:middle;border:2px solid #c8102e}
.brand{left:0;width:1200px;top:20px;text-align:center;font-size:27px;font-weight:700;color:var(--teal)}
.nav{left:0;width:1200px;top:73px;display:flex;justify-content:center;gap:28px;font-size:13px}
.nav .on{color:var(--salmon)}
.header .icons{right:140px;top:32px;display:flex;gap:34px}
.hero-title{left:0;top:282px;width:1200px;text-align:center;z-index:2;color:#fff;font-size:48px;font-weight:800}
.hero-btn{left:531px;top:350px;z-index:2;width:138px;text-align:center;padding:10px 0}

.band{left:0;width:1200px;height:63px;background:var(--band);overflow:hidden;white-space:nowrap}
.band span{position:absolute;top:10px;font-family:Oswald,Impact,sans-serif;font-size:31px;color:#fff;letter-spacing:.5px;text-transform:uppercase}

.camp{top:700px;width:600px;height:600px}
.camp .label{left:66px;top:425px;color:#fff}
.camp h3{font-weight:400;font-size:30px}
.camp a{display:inline-block;margin-top:10px;color:#fff;font-weight:700;font-size:19px;text-decoration:underline;text-underline-offset:5px}

.h2{left:0;width:1200px;text-align:center;font-weight:800;font-size:38px}
.feature{top:1493px;width:200px}
.feature .box{width:118px;height:118px;border:2px solid var(--teal);display:flex;align-items:center;justify-content:center}
.feature p{margin-top:15px;font-size:14px;line-height:20px;color:#444}

.step{top:1936px;width:400px;height:414px}
.step .label{left:44px;top:296px;color:#fff}
.step .n{font-size:20px}
.step .t{font-size:20px;font-weight:800;margin-top:12px}

.about-text{left:190px;width:820px;top:2500px;text-align:center;color:var(--text);font-size:14.5px;line-height:24px}
.about-text p+p{margin-top:24px}

.faq{width:446px;height:66px;border:1px solid var(--line);display:flex;justify-content:space-between;align-items:center;padding:0 24px;font-size:14px;color:#333}
.faq b{font-weight:400;font-size:22px;color:#555}

.news{left:0;top:4061px;width:1200px;height:400px;background:#f2efe9}
.news-text{left:565px;top:4170px;width:560px}
.news-text h2{font-size:38px;font-weight:700}
.news-text p{margin-top:18px;color:var(--text);font-size:15px;line-height:24px}

.footer{left:0;top:4522px;width:1200px;height:376px;background:var(--footer);color:#fff}
.f-brand{left:143px;top:78px;font-size:34px;font-weight:700;color:var(--teal)}
.f-about{left:143px;top:156px;width:330px;font-size:13.5px;line-height:20px}
.f-col h4{font-size:17px;font-weight:700;margin-bottom:14px}
.f-col li{list-style:none;font-size:14px;line-height:24px}
.f-col li::before{content:"»";margin-right:14px;color:#ccc}
.contact div{font-size:14px;margin-bottom:27px;display:flex;gap:10px;align-items:center}
.bottom{top:318px;left:0;width:1200px;font-size:13px}
.social{right:158px;top:311px;display:flex;gap:9px}
.social i{width:23px;height:23px;border-radius:50%;background:#2e2e2e;display:block}
.social i:first-child{background:var(--salmon)}
</style>
</head>
<body>

<div class="abs promo">Free expedited shipping for all orders over $99!</div>

<section class="abs hero" role="img" aria-label="Photo of girls sewing together at a table"></section>
<header class="abs header">
  <div class="abs tools">
    <svg width="14" height="14" viewBox="0 0 14 14"><circle cx="6" cy="6" r="4.5" fill="none" stroke="#fff" stroke-width="2"/><path d="M9 9l4 4" stroke="#fff" stroke-width="2"/></svg>
    <span><span class="flag"></span> Eng ⌄</span>
  </div>
  <div class="abs brand">Tiny-ThreadDays</div>
  <nav class="abs nav"><span class="on">Home</span><span>About</span><span>Upcoming Camp</span><span>Blog</span><span>FAQ</span><span>Contact</span></nav>
  <div class="abs icons">
    <svg width="12" height="14" viewBox="0 0 12 14"><circle cx="6" cy="4" r="3.5" fill="#fff"/><path d="M0 14c0-5 12-5 12 0z" fill="#fff"/></svg>
    <svg width="15" height="14" viewBox="0 0 15 14"><path d="M0 1h3l2 8h8l2-6H4" fill="none" stroke="#fff" stroke-width="2"/><circle cx="6" cy="12" r="1.5" fill="#fff"/><circle cx="12" cy="12" r="1.5" fill="#fff"/></svg>
  </div>
</header>
<h1 class="abs hero-title">Tiny-ThreadDays</h1>
<a class="abs btn hero-btn">Shop Now</a>

<div class="abs band" style="top:637px"><span style="left:23px">Upcoming Camp</span><span style="left:493px">Upcoming Camp</span><span style="left:963px">Upcoming Camp</span></div>

<section class="abs camp" style="left:0;background:radial-gradient(ellipse 220px 200px at 230px 200px,rgba(214,170,70,.55),transparent 70%),radial-gradient(ellipse 300px 200px at 420px 120px,rgba(170,180,175,.45),transparent 70%),linear-gradient(180deg,#7b8760 0%,#6c7748 45%,#495532 80%,#3a4428 100%)" role="img" aria-label="Photo of two children playing outdoors with a beach ball">
  <div class="abs label"><h3>Spring Camps</h3><a>View Details</a></div>
</section>
<section class="abs camp" style="left:600px;background:radial-gradient(ellipse 340px 180px at 300px 80px,rgba(200,210,225,.6),transparent 70%),radial-gradient(ellipse 300px 200px at 300px 420px,rgba(150,140,170,.5),transparent 70%),linear-gradient(180deg,#8e98a8 0%,#7a6f66 45%,#55505a 80%,#3e3a44 100%)" role="img" aria-label="Photo of a group of smiling children outdoors">
  <div class="abs label"><h3>Summer Camps</h3><a>View Details</a></div>
</section>

<h2 class="abs h2" style="top:1400px">Why Parents Choose Us</h2>
<div class="abs feature" style="left:143px"><div class="box"><svg width="60" height="60" viewBox="0 0 60 60" fill="none" stroke="#6fb0a6" stroke-width="2"><circle cx="18" cy="14" r="5"/><circle cx="30" cy="12" r="5"/><circle cx="42" cy="14" r="5"/><path d="M10 46V26h16v20M22 46V24h16v22M34 46V26h16v20"/></svg></div><p>Small groups &amp;<br>personalized attention</p></div>
<div class="abs feature" style="left:384px"><div class="box"><svg width="60" height="60" viewBox="0 0 60 60" fill="none" stroke="#6fb0a6" stroke-width="2"><rect x="22" y="8" width="30" height="24" rx="3"/><rect x="8" y="24" width="26" height="22" rx="3"/><path d="M14 40l7-12 7 12M16 36h10M30 14h14M37 11v4M33 24c4-2 7-6 8-10"/></svg></div><p>Multilingual supervision<br>(DE / EN / IT)</p></div>
<div class="abs feature" style="left:627px"><div class="box"><svg width="60" height="60" viewBox="0 0 60 60" fill="none" stroke="#6fb0a6" stroke-width="2"><path d="M8 34l22 12 22-12-22-12z"/><path d="M8 40l22 12 22-12"/><path d="M18 26c6-10 16-14 28-12-4 8-12 14-22 16"/></svg></div><p>High-quality fabrics &amp;<br>top-quality sewing<br>machines (Stitchwell)</p></div>
<div class="abs feature" style="left:873px"><div class="box"><svg width="60" height="60" viewBox="0 0 60 60" fill="none" stroke="#6fb0a6" stroke-width="2"><path d="M20 52V42c-6-4-9-10-8-17 1-9 9-15 18-15 10 0 17 7 17 16l4 8h-5v7h-8v11"/><path d="M24 18h8v6h8v8h-8v-4h-8z"/></svg></div><p>Encouragement of<br>creativity, self-confidence,<br>and fine motor skills</p></div>
<a class="abs btn" style="left:531px;top:1717px;width:138px;text-align:center;padding:10px 0">View More</a>

<div class="abs band" style="top:1873px"><span style="left:-7px">How the Camp Works</span><span style="left:452px">How the Camp Works</span><span style="left:922px">How the Camp Works</span></div>

<section class="abs step" style="left:0;background:radial-gradient(ellipse 160px 180px at 200px 160px,rgba(200,170,150,.45),transparent 70%),linear-gradient(180deg,#8c7f72 0%,#6b5e52 55%,#4a4038 100%)" role="img" aria-label="Photo of a girl cutting fabric with scissors"><div class="abs label"><div class="n">Step 01</div><div class="t">Project Selection</div></div></section>
<section class="abs step" style="left:400px;background:radial-gradient(ellipse 180px 120px at 140px 80px,rgba(210,120,140,.55),transparent 70%),radial-gradient(ellipse 160px 160px at 250px 300px,rgba(170,150,140,.5),transparent 70%),linear-gradient(180deg,#8e7c86 0%,#5f6f84 55%,#3e4a5a 100%)" role="img" aria-label="Photo of a child choosing colourful fabric"><div class="abs label"><div class="n">Step 02</div><div class="t">Fabric Selection</div></div></section>
<section class="abs step" style="left:800px;background:radial-gradient(ellipse 160px 180px at 180px 200px,rgba(220,190,160,.45),transparent 70%),linear-gradient(180deg,#d2ccc4 0%,#a69e94 55%,#6f685f 100%)" role="img" aria-label="Photo of a young girl working at a sewing machine"><div class="abs label"><div class="n">Step 03</div><div class="t">Sewing Machine</div></div></section>

<h2 class="abs h2" style="top:2438px">About Us</h2>
<div class="abs about-text">
  <p>Marta and Lena have over 10 years of experience in teaching children sewing, tailoring, and design with fun, style, and structure.</p>
  <p>In small groups (max. 8 children), we guide young talents through a creative week of vacation – with real results: self-sewn pieces, new friends, and lots of pride. At the last day, the children show off their success, their own sewn unique pieces, in a symapatic fashion show.</p>
</div>
<a class="abs btn" style="left:531px;top:2664px;width:138px;text-align:center;padding:10px 0">Learn More</a>
<div class="abs" style="left:312px;top:2753px;width:743px;height:380px;background:radial-gradient(ellipse 160px 100px at 380px 30px,rgba(190,50,50,.45),transparent 70%),linear-gradient(100deg,#5c5048 0%,#b58f78 40%,#d9b8a2 65%,#ece4de 100%)" role="img" aria-label="Photo of a teacher and a girl sewing together"></div>
<div class="abs" style="left:150px;top:2949px;width:375px;height:312px;background:#fff"></div>
<div class="abs" style="left:156px;top:2955px;width:363px;height:300px;background:radial-gradient(ellipse 120px 140px at 260px 130px,rgba(150,175,200,.6),transparent 70%),linear-gradient(100deg,#b8b4ae 0%,#d8d4ce 40%,#9fb3c2 70%,#8fa79a 100%)" role="img" aria-label="Photo of a smiling girl at a sewing machine"></div>

<div class="abs" style="left:0;top:3388px;width:1200px;height:2px;background:#777"></div>

<h2 class="abs h2" style="top:3482px">Frequently Asked Questions</h2>
<div class="abs faq" style="left:143px;top:3561px">Does my child need any prior knowledge?<b>+</b></div>
<div class="abs faq" style="left:610px;top:3561px">Lorem ipsum dolor sit amet, consectetur?<b>+</b></div>
<div class="abs faq" style="left:143px;top:3642px">How does the pick-up service work?<b>+</b></div>
<div class="abs faq" style="left:610px;top:3642px">Lorem ipsum dolor sit amet, consectetur?<b>+</b></div>
<div class="abs faq" style="left:143px;top:3722px">How many items of clothing are produced?<b>+</b></div>
<div class="abs faq" style="left:610px;top:3722px">Lorem ipsum dolor sit amet, consectetur?<b>+</b></div>
<div class="abs faq" style="left:143px;top:3803px">Lorem ipsum dolor sit amet, consectetur?<b>+</b></div>
<div class="abs faq" style="left:610px;top:3803px">Lorem ipsum dolor sit amet, consectetur?<b>+</b></div>
<div class="abs faq" style="left:143px;top:3883px">Lorem ipsum dolor sit amet, consectetur?<b>+</b></div>
<div class="abs faq" style="left:610px;top:3883px">Lorem ipsum dolor sit amet, consectetur?<b>+</b></div>

<section class="abs news"></section>
<div class="abs" style="left:0;top:4061px;width:760px;height:400px;background:radial-gradient(ellipse 160px 90px at 390px 310px,rgba(215,60,110,.45),transparent 75%),radial-gradient(ellipse 110px 140px at 420px 150px,rgba(215,160,130,.4),transparent 75%),linear-gradient(90deg,#e4e0da 0%,#ece8e2 60%,#f2efe9 100%)" role="img" aria-label="Photo of a laughing girl holding pink fabric beside a sewing machine"></div>
<div class="abs news-text">
  <h2>Register For Our Newsletter</h2>
  <p>Lorem ipsum dolor sit amet, consectetur adipiscing elit, sed do eiusmod tempor incididunt ut labore et dolore magna aliqua.</p>
  <a class="btn" style="margin-top:22px;padding:10px 30px">Learn More</a>
</div>

<div class="abs band" style="top:4461px"><span style="left:-10px">Register for Newsletter</span><span style="left:432px">Register for Newsletter</span><span style="left:902px">Register for Newsletter</span></div>

<footer class="abs footer">
  <div class="abs f-brand">Tiny-ThreadDays</div>
  <p class="abs f-about">Marta and Lena have over 10 years of experience in teaching children sewing, tailoring, and design with fun, style, and structure.</p>
  <div class="abs f-col" style="left:582px;top:82px"><h4>Quick Links</h4><ul><li>Home</li><li>About</li><li>Upcoming Camp</li><li>Blog</li><li>FAQ</li><li>Contact</li></ul></div>
  <div class="abs f-col contact" style="left:838px;top:82px"><h4>Contact Us</h4>
    <div><svg width="10" height="14" viewBox="0 0 10 14"><path d="M5 14S0 8 0 5a5 5 0 0110 0c0 3-5 9-5 9z" fill="#f2a894"/><circle cx="5" cy="5" r="2" fill="#1b1b1b"/></svg>Lorem ipsum dolor sit amet</div>
    <div><svg width="13" height="13" viewBox="0 0 13 13"><path d="M3 0l2 3-1.5 2a8 8 0 004 4L9.5 7.5l3 2L11 12C5 12 1 8 1 2z" fill="#f2a894"/></svg>+41 44 555 0199</div>
    <div><svg width="14" height="10" viewBox="0 0 14 10"><rect width="14" height="10" fill="#f2a894"/><path d="M0 0l7 5 7-5" fill="none" stroke="#1b1b1b"/></svg>info@tiny-threaddays.ch</div>
  </div>
  <div class="abs" style="left:143px;top:311px;font-size:13px;display:flex;gap:26px;align-items:center"><span><span class="flag" style="border-color:#3c5aa6"></span> USD ⌄</span><span><span class="flag"></span> Eng ⌄</span></div>
  <div class="abs bottom" style="text-align:center">© Copyrights 2025 | All Rights Reserved</div>
  <div class="abs social"><i></i><i></i><i></i><i></i></div>
  <div class="abs" style="right:60px;top:318px;font-size:11px;color:#bbb">CHF</div>
</footer>

</body>
</html>
```